Brightmoor Leaf is a bridge for the people who drink tea to connect with the people who make the tea and the environment in which it is grown.

As a start-up, Brightmoor Leaf needs to establish a fluently persuasive brand image that articulates its unique mission to the up-market tea drinker.

Our passion for high quality tea and our respect for people are boundless. But our budget is shoe-string. Still, we will allocate a disproportionate amount to evolving a brand; including logo, labeling, and packaging, and hope this initial effort will lead to a long-term relationship with a designer. The Brightmoor label, as a component of the brand, must deny the commodity image of tea by broadcasting the uniquely flavorful, healthful, and relaxing experience of drinking tea.

The logo is an image of a liquor pouring from above into a stylized outline of a cup and gracefully folding over on itself within the cup. The image is an echo of video clips that will be featured on the Product page of the ecommerce site. Our initial thought is for the liquor and cup to be white on a rich blue background. But you may have a better idea.

The label must fit a seamless tin canister 4" in diameter; 2" high with a "window" in the lid. There are really three distinct parts to the label: a) wrap-around for the body of the tin; b) a distinct piece to be applied underneath the tin; and c) security strip (s) that connect the lid and the bottom of the tin. The wrap-around must include the following components: the logo, the brand name 'Brightmoor Leaf', the name of the specific tea and space for the following characteristics of the tea: Tea / Garden Name, Harvest Date, Tasting Notes, Weight, Location, and Caffeine content. The piece to be affixed underneath the tin should accommodate Ingredients, Brewing Instructions, and contact details for Brightmoor Leaf. The security strip(s) should be an integral part of the overall visual.

The color scheme should be expandable, i.e.; different colors for different teas.
We are thinking about rich and bold colors. But am eager to see what inspires you!

A very rough proto-type is captured in the attached files.

Target Market(s)

Ages 25 to 45 in densely populated areas of the U.S. and Canada will an above average house-hold income and an interest in what they eat / drink.

Industry/Entity Type

Environment

Requirements
Must have
• 1. Three separate pieces: 1) wrap around for the body of the tin; 2) piece to be affixed to the bottom of the body of the tin; 3) security strip (s). A word about strips: am unsure about one vs two because, two will add to overhead and processing while one will block the view of the contents. Maybe you know how to resolve.
2. clean, crisp lines
3. uncluttered
Nice to have
• 1. a color scheme to accommodate up to 30 different teas. Do not fall into the trap of incorporating the color green on the label for a 'green tea' and yellow for a lemon flavored tea. That approach is limited and has been overdone.
2. a color scheme that, as it expands to accommodate 30 teas, also is anchored by a brand color set. In other words, all labels include a recognizable color set.
3. express the level of caffeine via a gauge or metric
Should not have
• photo images,

```html
<!DOCTYPE html>
<html lang="en">
<head>
<meta charset="utf-8">
<title>Brightmoor Leaf – Tin Label</title>
<link rel="stylesheet" href="https://fonts.googleapis.com/css2?family=Play:wght@400;700&display=swap">
<style>
  :root {
    --page: #ffffff;
    --label-blue: #2a3bfd;
    --label-edge: #5a5a6a;
    --title: #eadcf7;
    --tea-name: #f3a98c;
    --mark: #1fe6f0;
    --info-key: #a4f020;
    --info-value: #c9da1c;
    --gauge-on: #ff0a0a;
    --gauge-off: #ffffff;
    --gauge-edge: #1b1b55;
    --caffeine-ink: #111111;
    --box-edge: #3a46c8;
  }
  html, body {
    margin: 0;
    padding: 0;
    width: 1200px;
    height: 443px;
    overflow: hidden;
    background: var(--page);
  }
  .canvas {
    position: relative;
    width: 1200px;
    height: 443px;
    font-family: "Play", sans-serif;
  }
  .label {
    position: absolute;
    left: 0;
    top: 0;
    width: 1198px;
    height: 373px;
    background: var(--label-blue);
    border: 1px solid var(--label-edge);
  }
  .brand-title {
    position: absolute;
    left: 152px;
    top: 20px;
    margin: 0;
    font-size: 72px;
    font-weight: 400;
    line-height: 1;
    color: var(--title);
    letter-spacing: -1px;
    white-space: nowrap;
  }
  .brand-mark {
    position: absolute;
    left: 320px;
    top: 180px;
    width: 162px;
    display: flex;
    align-items: center;
    justify-content: center;
    gap: 8px;
    font-size: 18px;
    line-height: 1;
    color: var(--mark);
    white-space: nowrap;
  }
  .brand-mark .dot {
    width: 10px;
    height: 10px;
    background: var(--mark);
  }
  .tea-name {
    position: absolute;
    left: 246px;
    top: 282px;
    margin: 0;
    font-size: 54px;
    font-weight: 400;
    line-height: 1;
    letter-spacing: 2.3px;
    color: var(--tea-name);
    white-space: nowrap;
  }
  .caffeine-label {
    position: absolute;
    left: 5px;
    top: 266px;
    transform-origin: 0 0;
    transform: rotate(-90deg);
    font-size: 36px;
    letter-spacing: 2px;
    color: var(--caffeine-ink);
    border-bottom: 1.5px solid var(--caffeine-ink);
    line-height: 1;
    padding-bottom: 1px;
    white-space: nowrap;
  }
  .gauge {
    position: absolute;
    left: 52px;
    top: 62px;
    width: 40px;
    height: 250px;
    border: 1px solid var(--label-edge);
  }
  .gauge-cell {
    position: absolute;
    left: 8px;
    width: 25px;
    height: 33px;
    border: 1px solid var(--gauge-edge);
    box-sizing: border-box;
  }
  .gauge-cell.off { background: var(--gauge-off); }
  .gauge-cell.on { background: var(--gauge-on); }
  .info-box {
    position: absolute;
    left: 717px;
    top: 102px;
    width: 458px;
    height: 245px;
    border: 1px solid var(--box-edge);
  }
  .info-list {
    position: absolute;
    left: 18px;
    top: 17px;
    margin: 0;
    padding: 0;
    list-style: none;
  }
  .info-list li {
    height: 32.5px;
    font-size: 24px;
    line-height: 32px;
    color: var(--info-key);
    display: flex;
    align-items: center;
    white-space: nowrap;
  }
  .info-list li::before {
    content: "";
    width: 6px;
    height: 6px;
    margin: 0 14px 0 2px;
    background: var(--info-key);
    transform: rotate(45deg);
  }
  .info-values {
    position: absolute;
    left: 251px;
    top: 17px;
    margin: 0;
    padding: 0;
    list-style: none;
  }
  .info-values li {
    height: 34.5px;
    font-size: 25px;
    line-height: 34px;
    color: var(--info-value);
    white-space: nowrap;
  }
</style>
</head>
<body>
<div class="canvas">
  <section class="label">
    <span class="caffeine-label">Caffeine</span>
    <div class="gauge" role="img" aria-label="Caffeine level 3 of 5">
      <div class="gauge-cell off" style="top:18px"></div>
      <div class="gauge-cell off" style="top:62px"></div>
      <div class="gauge-cell on" style="top:106px"></div>
      <div class="gauge-cell on" style="top:149px"></div>
      <div class="gauge-cell on" style="top:192px"></div>
    </div>

    <h1 class="brand-title">Brightmoor Leaf</h1>

    <div class="brand-mark"><span class="dot"></span>Brightmoor Leaf</div>

    <h2 class="tea-name">Specific Tea</h2>

    <div class="info-box">
      <ul class="info-list">
        <li>Tea</li>
        <li>Garden</li>
        <li>Harvest Date</li>
        <li>Weight</li>
        <li>Location</li>
      </ul>
      <ul class="info-values">
        <li>Tea Type</li>
        <li>G. Name</li>
        <li>Date Here</li>
        <li>Weight</li>
        <li>Area</li>
      </ul>
    </div>
  </section>
</div>
</body>
</html>
```